Calloway Metal Recyclers - www.callowayrecyclers-example.com.au

I've just rebranded my business and thought what better way to continue with this than getting a website.
It is going to be fairly basic for now. I've attached quite a few images, feel free to use whichever you like.
And pages description is also attached in a .doc file.
Updates

Hi, this is my first time having a website. I am open to anything and trust the experience and ideas you can bring forward. I will look at extending the deadline so I can take my time to give feedback as needed! Thank you all.

Target Market(s)

Mining and industrial and commercial sectors

Coding

Coded - Design and coding required

Number of Pages Required

5+ page

Requirements
Must have
• Logo/Phone number at the top of every page. "Scrap Metal Specialists" tag line at the top of every page.
Nice to have
• Top Navigation.

```html
<!DOCTYPE html>
<html lang="en">
<head>
<meta charset="utf-8">
<title>Calloway Metal Recyclers</title>
<link href="https://fonts.googleapis.com/css2?family=Roboto+Slab:wght@400;700;800&family=Source+Serif+4:wght@400;600&family=Roboto+Condensed:wght@700&family=Roboto:wght@400;500&display=swap" rel="stylesheet">
<style>
:root{
  --navy:#1f3c74;
  --navy-deep:#17305f;
  --grey:#8a8d93;
  --grey-dark:#6f7278;
  --white:#ffffff;
  --ink:#1b1b1b;
  --body:#3c3c3c;
}
*{margin:0;padding:0;box-sizing:border-box}
html,body{width:1200px;height:3081px;overflow:hidden;background:var(--white)}
body{position:relative;font-family:"Source Serif 4",Georgia,serif;color:var(--body)}
.abs{position:absolute}

/* header */
.site-header{position:absolute;left:0;top:0;width:1200px;height:135px;background:var(--white);z-index:5}
.brand{position:absolute;left:95px;top:18px;width:200px;text-align:center;font-family:"Roboto Slab",serif;font-weight:800;color:var(--grey-dark);line-height:1}
.brand .name{font-size:34px;letter-spacing:1px}
.brand .sub{font-size:17px;color:var(--navy);margin-top:4px}
.brand .phone{font-size:19px;margin-top:3px;letter-spacing:1px}
.brand .tagline{font-family:"Roboto Slab",serif;font-weight:700;font-size:11px;letter-spacing:1.5px;color:var(--navy);margin-top:6px;text-transform:uppercase}
.topbar{position:absolute;left:385px;top:0;width:815px;height:67px}
.contact-item{position:absolute;top:10px;display:flex;align-items:center;gap:12px;color:var(--white)}
.contact-item .ic{width:42px;height:42px;border-radius:50%;background:var(--white);display:flex;align-items:center;justify-content:center}
.contact-item b{display:block;font-size:12px;font-weight:600}
.contact-item span{font-size:12px}
.main-nav{position:absolute;top:92px;left:345px;display:flex;font-family:"Source Serif 4",serif;font-size:16px;letter-spacing:1.5px;color:#222}
.main-nav a{color:inherit;text-decoration:none;margin-right:66px}

/* hero */
.hero{position:absolute;left:0;top:135px;width:1200px;height:710px}
.hero-photo{position:absolute;inset:0;background:linear-gradient(100deg,#2a4a86 0%,#3d5a8e 38%,#8a8e99 62%,#b8a98a 80%,#c7a04a 100%)}
.hero-shade{position:absolute;inset:0;background:linear-gradient(90deg,rgba(31,60,116,.98) 0%,rgba(31,60,116,.9) 40%,rgba(31,60,116,0) 65%)}
.hero-welcome{position:absolute;left:103px;top:172px;font-size:24px;letter-spacing:2px;color:var(--white);display:flex;align-items:center}
.hero-welcome i{display:inline-block;width:75px;height:2px;background:var(--white);margin-left:4px;margin-top:10px}
.hero-title{position:absolute;left:98px;top:222px;font-family:"Roboto Slab",serif;font-weight:800;color:var(--white);line-height:1}
.hero-title .l1{font-size:80px;letter-spacing:1px}
.hero-title .l2{font-size:52px;margin-top:2px}
.hero-text{position:absolute;left:100px;top:373px;width:440px;font-size:11.5px;line-height:21px;color:var(--white)}
.btn{position:absolute;display:flex;align-items:center;justify-content:center;background:var(--navy);color:var(--white);font-size:17px;border-top:4px solid var(--grey);border-left:4px solid var(--grey);box-shadow:3px 4px 8px rgba(0,0,0,.25)}

/* about */
.about-photo{position:absolute;left:93px;top:750px;width:439px;height:532px;background:linear-gradient(135deg,#c8d3dc 0%,#9a8f86 45%,#7d6d63 70%,#c7b59a 100%);box-shadow:0 25px 40px rgba(0,0,0,.3)}
.about-title{position:absolute;left:615px;top:833px;font-family:"Roboto Slab",serif;font-weight:800;font-size:52px;color:var(--ink)}
.about-rule{position:absolute;left:503px;top:906px;width:217px;height:2px;background:var(--navy)}
.about-text{position:absolute;left:615px;top:937px;width:505px;font-size:19px;line-height:34.5px;color:#333}

/* services */
.services-band{position:absolute;left:0;top:1418px;width:1200px;height:480px;background:linear-gradient(90deg,#213f77,#2a4a84)}
.service-item{position:absolute;left:100px;display:flex;gap:20px;color:var(--white)}
.service-item .ic{width:84px;height:84px;border-radius:50%;border:3px solid var(--white);display:flex;align-items:center;justify-content:center;flex:none}
.service-item .ic div{width:72px;height:72px;border-radius:50%;background:var(--white);display:flex;align-items:center;justify-content:center}
.service-item h3{font-family:"Roboto Slab",serif;font-weight:700;font-size:19px;margin-top:2px}
.service-item p{font-size:16px;line-height:26px;width:295px;margin-top:2px;padding-left:3px}
.services-box{position:absolute;left:539px;top:1450px;width:561px;height:410px;border:4px solid var(--white);color:var(--white)}
.services-box h2{position:absolute;left:96px;top:40px;font-family:"Roboto Slab",serif;font-weight:700;font-size:37px}
.services-box .rule{position:absolute;left:98px;top:100px;width:106px;height:2px;background:var(--white)}
.services-box p{position:absolute;left:98px;top:135px;width:430px;font-size:18.5px;line-height:29px}

/* targets */
.targets{position:absolute;left:0;top:1935px;width:1200px;height:680px;background:linear-gradient(180deg,#f3f4f6,#e4e7ec)}
.targets h2{position:absolute;left:0;width:1200px;top:124px;text-align:center;font-family:"Roboto Condensed",sans-serif;font-weight:700;font-size:40px;color:var(--ink)}
.targets .rule{position:absolute;left:563px;top:175px;width:78px;height:3px;background:var(--navy)}
.target{position:absolute;top:205px;width:312px;height:312px;border-radius:50%;border:4px solid var(--navy);overflow:hidden}
.target .ph{position:absolute;inset:0}
.target .label{position:absolute;left:0;right:0;bottom:0;height:76px;background:var(--navy);color:var(--white);font-size:21px;text-align:center;padding-top:12px}

/* footer */
.footer-logo{position:absolute;left:0;width:1200px;top:2640px;text-align:center;font-family:"Roboto Slab",serif;font-weight:800;color:var(--white);line-height:1}
.footer-logo .name{font-size:54px;letter-spacing:1px}
.footer-logo .sub{font-size:26px;margin-top:6px}
.footer-logo .phone{font-size:26px;margin-top:2px}
.footer-nav{position:absolute;top:2800px;left:203px;display:flex;font-family:"Roboto Slab",serif;font-weight:700;font-size:16px;letter-spacing:1.5px;color:var(--white)}
.footer-nav a{color:inherit;text-decoration:none;margin-right:66px}
.footer-rule{position:absolute;left:112px;top:2852px;width:976px;height:1px;background:rgba(255,255,255,.7)}
.f-head{position:absolute;top:2890px;font-family:"Roboto Slab",serif;font-weight:700;font-size:12.5px;color:var(--white)}
.f-line{position:absolute;font-family:"Roboto",sans-serif;font-size:14px;color:var(--white);line-height:23px}
.social{position:absolute;width:34px;height:34px;border:1px solid rgba(255,255,255,.8);display:flex;align-items:center;justify-content:center}
.social i{width:8px;height:8px;background:var(--white)}
.copy{position:absolute;left:0;width:1200px;top:3016px;text-align:center;font-family:"Roboto",sans-serif;font-size:14px;color:var(--white)}
</style>
</head>
<body>

<svg class="abs" style="left:0;top:2530px" width="1200" height="551" aria-hidden="true">
  <polygon points="0,65 1200,0 1200,551 0,551" fill="var(--grey)"/>
</svg>

<header class="site-header">
  <div class="brand">
    <div class="name">CALLOWAY</div>
    <div class="sub">METAL RECYCLERS</div>
    <div class="phone">0491 570 156</div>
    <div class="tagline">Scrap Metal Specialists</div>
  </div>
  <svg class="topbar" width="815" height="67" aria-hidden="true">
    <polygon points="0,0 815,0 815,67 37,67" fill="var(--navy)"/>
  </svg>
  <div class="contact-item" style="left:438px">
    <div class="ic"><svg width="16" height="20" viewBox="0 0 16 20"><path d="M8 0a7 7 0 0 0-7 7c0 5 7 13 7 13s7-8 7-13a7 7 0 0 0-7-7zm0 10a3 3 0 1 1 0-6 3 3 0 0 1 0 6z" fill="var(--navy)"/></svg></div>
    <div><b>Address</b><span>Lorem ipsum dolor sit amet</span></div>
  </div>
  <div class="contact-item" style="left:671px">
    <div class="ic"><svg width="20" height="15" viewBox="0 0 20 15"><rect x="1" y="1" width="18" height="13" rx="2" fill="none" stroke="var(--navy)" stroke-width="2"/><path d="M1 2l9 7 9-7" fill="none" stroke="var(--navy)" stroke-width="2"/></svg></div>
    <div><b>Email</b><span>info@callowaymetal-example.com</span></div>
  </div>
  <div class="contact-item" style="left:963px">
    <div class="ic"><svg width="18" height="18" viewBox="0 0 24 24"><path d="M6.6 10.8a15 15 0 0 0 6.6 6.6l2.2-2.2a1 1 0 0 1 1-.25 11.4 11.4 0 0 0 3.6.6 1 1 0 0 1 1 1V20a1 1 0 0 1-1 1A17 17 0 0 1 3 4a1 1 0 0 1 1-1h3.5a1 1 0 0 1 1 1c0 1.25.2 2.45.6 3.6a1 1 0 0 1-.25 1z" fill="var(--navy)"/></svg></div>
    <div><b>Call</b><span>+1 555-010-0199</span></div>
  </div>
  <nav class="main-nav">
    <a href="#">HOME</a><a href="#">ABOUT</a><a href="#">SERVICES</a><a href="#">ONLINE STORE</a><a href="#">BLOG</a><a href="#" style="margin-right:0">CONTACT</a>
  </nav>
</header>

<section class="hero">
  <div class="hero-photo" role="img" aria-label="Smiling scrap yard worker in hard hat and overalls beside an excavator grapple"></div>
  <div class="hero-shade"></div>
  <div class="hero-welcome">WELCOME TO<i></i></div>
  <h1 class="hero-title"><div class="l1">CALLOWAY</div><div class="l2">METAL RECYCLERS</div></h1>
  <p class="hero-text">Welcome to the website of Calloway Metal Recyclers. We are a Perth based company that provides scrap metal collection and oxy cutting services in the mining, construction, and industrial sectors all around WA.</p>
  <a class="btn" style="left:100px;top:460px;width:150px;height:50px">Get Started</a>
</section>
<svg class="abs" style="left:0;top:740px" width="1200" height="105" aria-hidden="true">
  <polygon points="0,103 1200,3 1200,105 0,105" fill="var(--white)"/>
</svg>

<section class="about">
  <div class="about-photo" role="img" aria-label="Worker in hard hat and safety glasses standing in a scrap metal yard"></div>
  <h2 class="about-title">ABOUT</h2>
  <div class="about-rule"></div>
  <p class="about-text">&nbsp;My name is Ben Calloway and I’m the managing director of Calloway Metal Processors. I have been in the scrap metal recycling industry longer than I haven’t! I have 16 years’ experience in everything scrap metal and I am very passionate about sustainable recycling</p>
  <a class="btn" style="left:615px;top:1145px;width:148px;height:48px">Get Started</a>
</section>

<section class="services">
  <div class="services-band" role="img" aria-label="Faint industrial plant skyline in navy tones"></div>
  <svg class="abs" style="left:548px;top:1385px" width="652" height="550" aria-label="Industrial refinery scene in grey tones" role="img">
    <defs><linearGradient id="svcGrey" x1="0" y1="0" x2="1" y2="1"><stop offset="0" stop-color="#8b8e95"/><stop offset="1" stop-color="#6e7279"/></linearGradient></defs>
    <polygon points="69,0 652,0 652,550 0,550" fill="url(#svcGrey)"/>
  </svg>

  <div class="service-item" style="top:1475px">
    <div class="ic"><div><svg width="40" height="40" viewBox="0 0 40 40"><path d="M8 8c6-4 14 0 16 8l6 14" fill="none" stroke="#111" stroke-width="2.5"/><path d="M27 26l6 10-3 1-5-9z" fill="#111"/></svg></div></div>
    <div><h3>Oxy cutting and breaking down</h3><p>Lorem ipsum dolor sit amet, consectetur adipiscing elit, sed</p></div>
  </div>
  <div class="service-item" style="top:1612px">
    <div class="ic"><div><svg width="44" height="40" viewBox="0 0 44 40"><rect x="8" y="10" width="24" height="14" rx="2" fill="none" stroke="#111" stroke-width="2"/><circle cx="14" cy="30" r="5" fill="none" stroke="#111" stroke-width="2"/><circle cx="30" cy="30" r="5" fill="none" stroke="#111" stroke-width="2"/><path d="M32 16h8v10h-8" fill="none" stroke="#111" stroke-width="2"/></svg></div></div>
    <div><h3>Large mining machinery</h3><p>up to 800t excavators, haul packs, loaders, buckets, booms</p></div>
  </div>
  <div class="service-item" style="top:1750px">
    <div class="ic"><div><svg width="46" height="36" viewBox="0 0 46 36"><path d="M4 6h38l-5 14H9z" fill="none" stroke="#111" stroke-width="2"/><circle cx="13" cy="27" r="6" fill="none" stroke="#111" stroke-width="2"/><circle cx="33" cy="27" r="6" fill="none" stroke="#111" stroke-width="2"/></svg></div></div>
    <div><h3>Large minesite infrastructure</h3><p>tanks, conveyors, crushers, SAG and ball mills</p></div>
  </div>

  <div class="services-box">
    <h2>OUR SERVICES</h2>
    <div class="rule"></div>
    <p>Sed ut perspiciatis unde omnis iste natus error sit voluptatem accusantium doloremque laudantium, totam rem aperiam, eaque ipsa quae ab illo inventore veritatis et quasi architecto beatae vitae dicta sunt explicabo.</p>
    <a class="btn" style="left:98px;top:320px;width:146px;height:46px;border:0;box-shadow:none">Read More</a>
  </div>
</section>

<section class="targets" aria-label="Our targets">
  <div class="abs" style="inset:0;background:linear-gradient(135deg,rgba(220,224,230,.6),rgba(245,246,248,.2))" role="img" aria-label="Faded pile of scrap metal with an excavator"></div>
  <h2>OUR TARGETS</h2>
  <div class="rule"></div>
  <div class="target" style="left:106px">
    <div class="ph" role="img" aria-label="Large yellow mining haul truck" style="background:linear-gradient(180deg,#c9d3dd 0%,#a9a49a 40%,#c09a3c 65%,#6f6a63 100%)"></div>
    <div class="label">MINING</div>
  </div>
  <div class="target" style="left:447px">
    <div class="ph" role="img" aria-label="Interior of a large industrial factory hall" style="background:linear-gradient(180deg,#3a6e95 0%,#7c8a90 40%,#3c4650 100%)"></div>
    <div class="label">INDUSTRIAL</div>
  </div>
  <div class="target" style="left:787px">
    <div class="ph" role="img" aria-label="Engineers in hi-vis vests at a commercial construction site" style="background:linear-gradient(180deg,#b9cee0 0%,#8a7a6a 50%,#c8c24a 75%,#5a5048 100%)"></div>
    <div class="label">COMMERCIAL</div>
  </div>
</section>
<svg class="abs" style="left:0;top:2530px" width="1200" height="90" aria-hidden="true">
  <polygon points="0,65 1200,0 1200,90 0,90" fill="var(--grey)"/>
</svg>

<footer>
  <div class="footer-logo">
    <div class="name">CALLOWAY</div>
    <div class="sub">METAL RECYCLERS</div>
    <div class="phone">0491 570 156</div>
  </div>
  <nav class="footer-nav">
    <a href="#">HOME</a><a href="#">ABOUT</a><a href="#">SERVICES</a><a href="#">ONLINE STORE</a><a href="#">BLOG</a><a href="#" style="margin-right:0">CONTACT</a>
  </nav>
  <div class="footer-rule"></div>

  <div class="f-head" style="left:124px">OFFICE LOCATION</div>
  <svg class="abs" style="left:124px;top:2922px" width="10" height="14" viewBox="0 0 16 20"><path d="M8 0a7 7 0 0 0-7 7c0 5 7 13 7 13s7-8 7-13a7 7 0 0 0-7-7zm0 10a3 3 0 1 1 0-6 3 3 0 0 1 0 6z" fill="var(--white)"/></svg>
  <div class="f-line" style="left:146px;top:2917px;width:170px">"Lorem ipsum dolor sit amet, consectetur</div>

  <div class="f-head" style="left:512px">CONTACT US</div>
  <svg class="abs" style="left:512px;top:2922px" width="14" height="14" viewBox="0 0 24 24"><path d="M6.6 10.8a15 15 0 0 0 6.6 6.6l2.2-2.2a1 1 0 0 1 1-.25 11.4 11.4 0 0 0 3.6.6 1 1 0 0 1 1 1V20a1 1 0 0 1-1 1A17 17 0 0 1 3 4a1 1 0 0 1 1-1h3.5a1 1 0 0 1 1 1c0 1.25.2 2.45.6 3.6a1 1 0 0 1-.25 1z" fill="var(--white)"/></svg>
  <div class="f-line" style="left:544px;top:2915px;font-size:17px;font-weight:500">+ 1 0491570156</div>
  <svg class="abs" style="left:512px;top:2956px" width="15" height="11" viewBox="0 0 20 15"><rect x="0" y="0" width="20" height="15" fill="var(--white)"/><path d="M0 1l10 7 10-7" fill="none" stroke="var(--grey)" stroke-width="2"/></svg>
  <div class="f-line" style="left:544px;top:2949px">ben@callowayrecyclers-example.com.au</div>

  <div class="social" style="left:1014px;top:2889px"><i></i></div>
  <div class="social" style="left:1057px;top:2889px"><i></i></div>
  <div class="social" style="left:1014px;top:2930px"><i></i></div>
  <div class="social" style="left:1057px;top:2930px"><i></i></div>

  <div class="copy">© 2022 Callowayrecyclers. All Rights Reserved</div>
</footer>

</body>
</html>
```